Flyer, poster, banner and social media titles designs for Community Mending Chartre

The Harbourline Charter for Community Mending provide a nationally agreed framework to guide recovery policy and practice across Australia. The Principles support recovery practitioners, governments, non-government organisations and communities to deliver effective, community-centred recovery outcomes.
The Principles have recently been refreshed through extensive consultation and we require a contemporary visual identity and design suite that will increase awareness, engagement and practical application of the Principles.
The redesign will cover:
• A4 Brochure (primary publication)
• A3 Poster
• Pull up banner
• Social Media Tiles
The new design should:
• Create a recognisable brand for the Harbourline Charter.
• Appeal to both experienced and emerging recovery practitioners.
• Reflect contemporary disaster recovery practice.
• Feel people-focused rather than government-focused.
• Support future resources such as videos, implementation guides, presentations and workshop materials.
• Remain relevant for several years without requiring a major redesign.
Target Audience
• Disaster recovery practitioners
• Government agencies
• Non-government organisations
• Community recovery workers
• Recovery managers and leaders
• Community stakeholders and volunteers
The visual identity should reflect the six Principles:
• Understanding Context
• Recognising Complexity
• Community-Centred Approaches
• Coordination
• Communication
• Capacity Building
The design should communicate:
• Recovery is centred on people and communities.
• Recovery is collaborative and involves many sectors.
• Recovery is adaptive, inclusive and evidence-informed.
• Recovery supports resilience and long-term wellbeing.
• The Principles provide practical guidance for recovery practice.
We are looking for:
• Modern and professional
• Warm and approachable
• Human-centred
• Inclusive and accessible
• Australian in context
• Visually engaging
• Suitable for print and digital use
We would like to avoid:
• Images of disaster destruction
• Emergency response imagery (fire trucks, flashing lights, etc.)
• Overly corporate or bureaucratic designs
• Designs that focus on deficits rather than recovery and growth
Consider themes such as:
• Connection and collaboration
• Communities and people
• Growth, recovery and renewal
Accessibility
Designs should:
• Meet accessibility best practice
• Use clear typography
• Achieve strong colour contrast
• Be suitable for both digital and print formats

Deliverables
1. Principles Brochure
• A4 trifold size x 2 (online and print friendly version)
• A side to include cover side, logos side and overview of principles.
• B side full details of the principles
• Graphic to highlight the 3 c’s concept (RECOVERY Context, complexity, community centred, coordinate, communicate and capacity). Currently 3 circles.
• Can be printed and distributed electronically
2. Poster
• A1 and A3 versions
• Suitable for office and workshop display
3. Pull-Up Banner - 850 mm (W) × 2000 mm (H)
• Conference and event use
• High visual impact
• Strong branding and concise messaging
4. Social Media Tiles x 3

We are providing an extension and increasing the budget following feedback from designers. We are wanting the resources to look and feel different from the existing designs, considering either a different colour palette in the designs or different motif with the leave design. Any nature based designs should consider the Australian fauna or flora. Also suggest avoiding images in the designs. The principles are not numbered or liner in the concept of how they function. Happy to answer any further questions and thank you for your suggested concepts.

Disaster recovery practitioners, Government agencies , Non-government organisations, Community recovery workers and Community stakeholders and volunteers

Disaster recovery

• Modern, warm, visually engaging, human-centred, Australian in context and different to the current design.
• Symbols for each principles
• Images of disaster destruction, Emergency response imagery, Overly corporate or bureaucratic designs, Designs that focus on deficits rather than recovery and growth, avoid too much black

```html
<!DOCTYPE html>
<html lang="en">
<head>
<meta charset="utf-8">
<title>Harbourline Charter for Community Mending – Trifold Brochure</title>
<link href="https://fonts.googleapis.com/css2?family=Montserrat:wght@500;700;800&family=Roboto:wght@400;500;700&family=Hind:wght@300;500&display=swap" rel="stylesheet">
<style>
:root{
  --bg:#b5b5b5;
  --deep:#1f4d4a;
  --paper:#f7f1e6;
  --wattle:#e3a72f;
  --clay:#c4633d;
  --gum:#7fa88f;
  --white:#ffffff;
  --ink:#2d3a38;
  --rule:#e0d6c4;
}
*{box-sizing:border-box;margin:0;padding:0}
html,body{width:790px;height:1200px;overflow:hidden;background:var(--bg)}
body{font-family:"Roboto",Arial,sans-serif;color:var(--ink);position:relative}
.spread{position:absolute;left:47px;width:695px;height:536px;display:flex;box-shadow:0 6px 14px rgba(0,0,0,.25)}
.spread--outside{top:46px}
.spread--inside{top:617px}
.panel{width:231.7px;height:100%;position:relative;overflow:hidden}
.panel--dark{background:var(--deep);color:var(--white)}
.panel--light{background:var(--paper)}

/* cover-left panel */
.intro{padding:20px 24px 0 25px}
.intro__kicker{font-family:"Montserrat",sans-serif;font-weight:700;font-size:10px;letter-spacing:.2px}
.intro__title{font-family:"Montserrat",sans-serif;font-weight:800;font-size:23px;line-height:27px;margin-top:6px;letter-spacing:.3px}
.intro__title span{display:block}
.intro__title .accent{color:var(--wattle)}
.intro__body{font-size:7.6px;line-height:10.5px;text-align:justify;margin-top:10px;font-weight:400}
.intro__body p+p{margin-top:10.5px}
.principle-list{list-style:none;margin-top:12px}
.principle-list li{font-size:8.2px;position:relative;padding-left:18px;height:19.4px;line-height:12px}
.principle-list li::before{content:"";position:absolute;left:1px;top:2px;width:8px;height:8px;border-radius:50%;background:var(--wattle)}
.principle-list li::after{content:"";position:absolute;left:3.6px;top:3.4px;width:2px;height:3.4px;border:solid var(--deep);border-width:0 1.2px 1.2px 0;transform:rotate(45deg)}

/* partners panel */
.partners{padding:12px 20px 0 23px}
.partner-grid{display:grid;grid-template-columns:1fr 1fr;width:188px}
.partner{height:72px;display:flex;align-items:center;justify-content:center;flex-direction:column;gap:4px;border-bottom:1px solid var(--rule);text-align:center;font-weight:500;font-size:7.2px;line-height:9px;color:var(--ink);padding:0 4px}
.partner:nth-child(odd){border-right:1px solid var(--rule)}
.partner .dot{width:22px;height:22px;border-radius:50%;background:#ddd2bd}
.partner--row1{height:62px}
.partner--row3{height:76px}
.partner--row4{height:84px}
.partner--row5{height:51px}
.partner--wide{grid-column:1 / 3;border-right:none !important;height:59px;flex-direction:row;justify-content:flex-start;gap:6px;text-align:left}
.partners__heading{font-family:"Montserrat",sans-serif;font-weight:700;font-size:10px;line-height:15px;margin-top:26px;color:var(--deep)}
.partners__lead{display:flex;align-items:center;gap:8px;margin-top:14px;font-size:7.4px;line-height:9px}
.partners__lead .dot{width:36px;height:36px;border-radius:50%;background:#cfe0d6}

/* cover-right panel */
.cover__band{height:118px;padding:18px 14px}
.cover__kicker{font-family:"Hind",sans-serif;font-weight:300;font-size:11px;letter-spacing:.3px}
.cover__title{font-family:"Hind",sans-serif;font-weight:500;font-size:33px;line-height:29px;margin-top:6px}
.cover__title span{display:block}
.cover__title .accent{color:var(--wattle)}
.cover__graphic{position:absolute;left:0;top:118px;width:100%;height:418px;background:var(--paper)}
.cover__graphic svg{display:block}

/* inside columns */
.col-head{height:64px;background:var(--wattle);color:var(--deep);text-align:center;font-weight:700;font-size:9px;line-height:12.5px;padding-top:9px}
.col-foot{position:absolute;left:0;bottom:0;width:100%;height:65px;background:var(--clay);color:var(--white);text-align:center;font-weight:700;font-size:9px;line-height:12.5px;padding-top:32px}
.badge{position:absolute;left:50%;width:48px;height:48px;margin-left:-24px;border-radius:50%;background:var(--white);border:2px solid var(--wattle);display:flex;align-items:center;justify-content:center}
.badge--top{top:40px}
.badge--bottom{bottom:41px;border-color:var(--clay)}
.col-body{padding:0 7px}
.col-body--dark{padding-top:30px}
.col-body--light{padding-top:8px}
.lead{font-size:7.6px;line-height:10px}
.points{list-style:none;margin-top:8px}
.points li{font-size:6.6px;line-height:8.3px;position:relative;padding-left:13px;margin-bottom:8.2px}
.points li::before{content:"";position:absolute;left:0;top:1px;width:6px;height:6px;border-radius:50%;background:var(--wattle)}
.points li::after{content:"";position:absolute;left:2px;top:1.8px;width:1.5px;height:2.6px;border:solid var(--deep);border-width:0 1px 1px 0;transform:rotate(45deg)}
.points--light li::before{background:var(--gum)}
.points--light li::after{border-color:var(--white)}
.panel--light .lead,.points--light li{color:var(--ink)}
.pad-top{padding-top:17px}
</style>
</head>
<body>

<section class="spread spread--outside">
  <article class="panel panel--dark intro">
    <p class="intro__kicker">HARBOURLINE CHARTER FOR</p>
    <h1 class="intro__title"><span>COMMUNITY</span><span class="accent">MENDING</span></h1>
    <div class="intro__body">
      <p>Disasters can deeply impact lives and livelihoods. Working with communities recovering from disasters is complex and challenging. Recovery is long-term, non-linear and dynamic, particularly in the context of compounding and concurrent disasters. These principles are a way to guide our efforts, our approach, our planning and our decision-making. Disaster recovery is part of emergency management, which includes the broader components of prevention, preparedness and response. Planning for recovery is integral to emergency preparation, and mitigation actions are often initiated as part of recovery.</p>
      <p>Disaster recovery includes built, environmental and economic elements, as well as individual and social wellbeing. Recovery can provide an opportunity to improve these aspects beyond previous conditions, by enhancing social and natural environments, infrastructure and economies –contributing to more resilient communities. The relationship between the principles While all the principles are equally critical to ensure effective recovery, understanding the local and broader context and recognising complexity are foundational. The descriptions beneath each principle provide further guidance for working with communities in disaster recovery.</p>
    </div>
    <ul class="principle-list">
      <li>Understand the CONTEXT</li>
      <li>Recognise COMPLEXITY</li>
      <li>Use COMMUNITY-CENTRED approaches</li>
      <li>COORDINATE all activities</li>
      <li>COMMUNICATE effectively</li>
      <li>Recognise and build CAPACITY</li>
    </ul>
  </article>

  <article class="panel panel--light partners">
    <div class="partner-grid">
      <div class="partner partner--row1">Federal Office of<br>Community Services</div>
      <div class="partner partner--row1">Federal Office of<br>Civic Safety</div>
      <div class="partner"><span class="dot"></span>Southern Relief Society</div>
      <div class="partner"><span class="dot"></span>Coralbay State<br>Government</div>
      <div class="partner partner--row3"><span class="dot"></span>Westreach State<br>Government</div>
      <div class="partner partner--row3"><span class="dot"></span>Islandmere<br>Government</div>
      <div class="partner partner--row4"><span class="dot"></span>Sunridge<br>Government</div>
      <div class="partner partner--row4"><span class="dot"></span>Capital Ridge<br>Government</div>
      <div class="partner partner--row5">Redsand Territory<br>Government</div>
      <div class="partner partner--row5">Southvale State<br>Government</div>
      <div class="partner partner--wide"><span class="dot"></span>Eastcoast Office of<br>Recovery Management</div>
    </div>
    <h2 class="partners__heading">PARTNERS IN DEVELOPMENT<br>FROM THE</h2>
    <div class="partners__lead"><span class="dot"></span>Community Recovery<br>Advisory Circle</div>
  </article>

  <article class="panel panel--dark cover">
    <div class="cover__band">
      <p class="cover__kicker">HARBOURLINE CHARTER FOR</p>
      <h1 class="cover__title"><span>Community</span><span class="accent">Mending</span></h1>
    </div>
    <div class="cover__graphic">
      <svg width="232" height="418" viewBox="0 0 232 418" role="img" aria-label="Three overlapping circles joining the six principles around recovery">
        <g style="mix-blend-mode:multiply">
          <circle cx="116" cy="150" r="66" fill="#e3a72f" opacity=".85"/>
          <circle cx="78" cy="215" r="66" fill="#7fa88f" opacity=".85"/>
          <circle cx="154" cy="215" r="66" fill="#c4633d" opacity=".85"/>
        </g>
        <g font-family="Roboto, Arial, sans-serif" font-weight="700" fill="#1f4d4a" text-anchor="middle" font-size="8.5">
          <text x="116" y="118">CONTEXT</text>
          <text x="116" y="130">COMPLEXITY</text>
        </g>
        <g font-family="Roboto, Arial, sans-serif" font-weight="700" fill="#ffffff" text-anchor="middle" font-size="8.5">
          <text x="60" y="236">COMMUNITY</text>
          <text x="60" y="248">COORDINATE</text>
          <text x="172" y="236">COMMUNICATE</text>
          <text x="172" y="248">CAPACITY</text>
        </g>
        <circle cx="116" cy="194" r="20" fill="#1f4d4a"/>
        <text x="116" y="197" font-family="Roboto, Arial, sans-serif" font-weight="700" font-size="6.5" fill="#ffffff" text-anchor="middle">RECOVERY</text>
        <text x="116" y="330" font-family="Hind, Arial, sans-serif" font-weight="500" font-size="11" fill="#1f4d4a" text-anchor="middle">Six principles, one shared path</text>
        <line x1="86" y1="342" x2="146" y2="342" stroke="#e3a72f" stroke-width="2"/>
      </svg>
    </div>
  </article>
</section>

<section class="spread spread--inside">
  <article class="panel panel--dark">
    <h2 class="col-head">Understand the<br>CONTEXT</h2>
    <div class="badge badge--top"><svg width="26" height="26" viewBox="0 0 26 26"><circle cx="13" cy="13" r="11" fill="none" stroke="#1f4d4a" stroke-width="2"/><circle cx="13" cy="13" r="4" fill="#e3a72f"/></svg></div>
    <div class="col-body col-body--dark">
      <p class="lead">Successful recovery is based on an understanding of the community context, with each community having its own history, values and dynamics. Recovery should:</p>
      <ul class="points">
        <li>Acknowledge existing strengths and capacity, including past experiences and future aspirations;</li>
        <li>Appreciate the risks and stressors faced by the community;</li>
        <li>Embed accessibility, equity, inclusion and diversity in recovery practice, using culturally safe and trauma -informed approaches;</li>
        <li>Support people who may be at greater risk or disproportionately impacted;</li>
        <li>Respect and support connections to Country, environment, animals and culturally significant places and recognise environmental regeneration in recovery;</li>
        <li>Recognise pathways and timeframes vary; systems should support long-term recovery shaped by community needs; and</li>
        <li>Acknowledge the impact upon the community may extend beyond the geographical boundaries where the disaster occurred.</li>
      </ul>
    </div>
  </article>

  <article class="panel panel--light">
    <div class="col-body col-body--light">
      <p class="lead">Successful recovery is responsive to the complex and evolving nature of disasters and their impacts on communities</p>
      <ul class="points points--light">
        <li>Disasters lead to a range of effects and impacts that require a variety of approaches; they can also leave long-term legacies;</li>
        <li>Information on impacts and needs can be limited at first and changes over time;</li>
        <li>Affected individuals and the community have diverse needs, wants and expectations, which can evolve rapidly;</li>
        <li>Responsive and flexible action is crucial to addressing immediate needs;</li>
        <li>Existing community knowledge and values may challenge the assumptions of those outside of the community;</li>
        <li>Conflicting knowledge, values and priorities among individuals, the community and organisations may create tensions;</li>
        <li>Emergencies create stressful environments where grief or blame may also affect those involved; and</li>
        <li>Over time, appropriate support for individuals and communities, from within and outside, can cultivate hope and individual and collective growth.</li>
      </ul>
    </div>
    <h2 class="col-foot">Recognise<br>COMPLEXITY</h2>
    <div class="badge badge--bottom"><svg width="26" height="26" viewBox="0 0 26 26"><rect x="4" y="15" width="4" height="7" fill="#1f4d4a"/><rect x="11" y="11" width="4" height="11" fill="#1f4d4a"/><rect x="18" y="7" width="4" height="15" fill="#1f4d4a"/><path d="M3 12 L10 7 L14 9 L22 3" fill="none" stroke="#c4633d" stroke-width="2"/></svg></div>
  </article>

  <article class="panel panel--dark">
    <h2 class="col-head">Use COMMUNITY<br>CENTRED Approaches</h2>
    <div class="badge badge--top"><svg width="26" height="26" viewBox="0 0 26 26"><circle cx="13" cy="13" r="3.5" fill="#e3a72f"/><g stroke="#1f4d4a" stroke-width="2" stroke-linecap="round"><line x1="13" y1="3" x2="13" y2="7"/><line x1="13" y1="19" x2="13" y2="23"/><line x1="3" y1="13" x2="7" y2="13"/><line x1="19" y1="13" x2="23" y2="13"/><line x1="6" y1="6" x2="9" y2="9"/><line x1="17" y1="17" x2="20" y2="20"/><line x1="20" y1="6" x2="17" y2="9"/><line x1="9" y1="17" x2="6" y2="20"/></g></svg></div>
    <div class="col-body col-body--dark">
      <p class="lead">Successful recovery is community-centred, responsive and flexible, engaging with community and supporting them to move forward, with shared responsibilities. Recovery should:</p>
      <ul class="points">
        <li>Assist and enable individuals, families and the community to actively participate in their own recovery;</li>
        <li>Recognise that individuals and the community may need different levels of support at various times;</li>
        <li>Be guided by the communities' priorities;</li>
        <li>Channel effort through pre-identified and existing community assets, including local knowledge, existing community strengths and resilience;</li>
        <li>Build collaborative partnerships that reflect diverse representation and community leadership in recovery;</li>
        <li>Support Aboriginal and Torres Strait Islander self-determination and Indigenous governance, recognising Country as central to recovery and resilience;</li>
        <li>Recognise that new community leaders often emerge during and after a disaster, who may not hold formal positions of authority; and</li>
      </ul>
    </div>
  </article>

  <article class="panel panel--light">
    <div class="col-body col-body--light">
      <p class="lead">Successful recovery requires a planned, coordinated and adaptive approach, between community and partner agencies, based on continuing assessment of impacts and need. Recovery should:</p>
      <ul class="points points--light">
        <li>Have clearly articulated and shared goals based on desired outcomes;</li>
        <li>Be flexible, taking into account changes in community needs or stakeholder expectations.</li>
        <li>Be guided by those with experience and expertise, using skilled, authentic and capable community leadership;</li>
        <li>Be at the pace desired by the community, and seek to collaborate and reconcile different interests and time frames;</li>
        <li>Reflect well-developed community planning and information gathering before, during and after a disaster;</li>
        <li>Have clear decision-making and reporting structures and sound governance, which are transparent and accessible to the community;</li>
        <li>Demonstrate an understanding of the roles, responsibilities and authority of organisations involved and coordinate across agencies to ensure minimal service provision disruption;</li>
      </ul>
    </div>
    <h2 class="col-foot">COORDINATE<br>All Activities</h2>
    <div class="badge badge--bottom"><svg width="26" height="26" viewBox="0 0 26 26"><circle cx="13" cy="13" r="10" fill="none" stroke="#1f4d4a" stroke-width="2" stroke-dasharray="3 2"/><circle cx="13" cy="6" r="2.5" fill="#c4633d"/><circle cx="7" cy="17" r="2.5" fill="#c4633d"/><circle cx="19" cy="17" r="2.5" fill="#c4633d"/></svg></div>
  </article>

  <article class="panel panel--dark">
    <h2 class="col-head">COMMUNICATE<br>Effectively</h2>
    <div class="badge badge--top"><svg width="26" height="26" viewBox="0 0 26 26"><path d="M4 5 H22 V16 H12 L7 21 V16 H4 Z" fill="none" stroke="#1f4d4a" stroke-width="2" stroke-linejoin="round"/><circle cx="9" cy="10.5" r="1.4" fill="#e3a72f"/><circle cx="13" cy="10.5" r="1.4" fill="#e3a72f"/><circle cx="17" cy="10.5" r="1.4" fill="#e3a72f"/></svg></div>
    <div class="col-body col-body--dark">
      <p class="lead">Successful recovery is built on effective communication between the affected community and other partners. Recovery should:</p>
      <ul class="points">
        <li>Recognise that communication should be two-way, transparent and ongoing, building trust through shared understanding and feedback;</li>
        <li>Ensure that information is accessible to audiences in diverse situations, addresses a variety of communication needs, and is provided through a range of communication channels and networks;</li>
        <li>Establish mechanisms for coordinated and consistent communications between all service providers, organisations and individuals and the community;</li>
        <li>Ensure that all communication is relevant, timely, clear, accurate, targeted, credible and consistent; and</li>
        <li>Identify trusted sources of information and repeat key recovery messages to enable greater community confidence and receptivity.</li>
      </ul>
    </div>
  </article>

  <article class="panel panel--light">
    <div class="col-body col-body--light pad-top">
      <p class="lead">Successful recovery recognises, supports and builds on individual, community and organisational capacity and resilience. Recovery should</p>
      <ul class="points points--light">
        <li>Assess capability and capacity requirements before, during and after a disaster;</li>
        <li>Support the development of self-reliance, preparation and disaster mitigation;</li>
        <li>Quickly identify and mobilise community skills, strengths and resources;</li>
        <li>Develop networks and partnerships to strengthen capacity, capability and resilience;</li>
        <li>Support training and knowledge sharing to sustain recovery capability across staff, volunteers, and the community;</li>
        <li>Ensure mental health and wellbeing supports are available for staff, volunteers and communities involved in disaster recovery;</li>
        <li>Recognise that resources can be provided by a range of partners and from community networks;</li>
        <li>Acknowledge that existing resources may be stretched, and that additional resources may be required;</li>
      </ul>
    </div>
    <h2 class="col-foot">Recognise And Build<br>CAPACITY</h2>
    <div class="badge badge--bottom"><svg width="26" height="26" viewBox="0 0 26 26"><rect x="5" y="6" width="16" height="15" rx="2" fill="#1f4d4a"/><path d="M10 13 A3.5 3.5 0 1 0 13 9.5" fill="none" stroke="#fff" stroke-width="1.6"/><path d="M13 7.5 L15 9.5 L13 11.5" fill="none" stroke="#fff" stroke-width="1.4"/></svg></div>
  </article>
</section>

</body>
</html>
```